Bluecrest Learning Corps by graduating students from college in two years

Based on the logo design, create stationary and business cards for
Dr. Venrel T Oskamp, CEO, (703) 482-1736
and Marisa Deltoft, Respresentative, (301) 647-2208
Address: 4719 Pellham Court, Faurfax Station, VA 22039
Incorporate elelments of the logo

Target Market(s)

USA

Font styles to use
Other font styles liked:
• match with the logo type style

```html
<!DOCTYPE html>
<html lang="en">
<head>
<meta charset="utf-8">
<title>Bluecrest Learning Corps — Letterhead</title>
<link rel="stylesheet" href="https://fonts.googleapis.com/css2?family=Arimo:wght@400;700&family=Montserrat:wght@600;700&display=swap">
<style>
  :root {
    --navy: #0f1f5c;
    --gold: #f6c22e;
    --ink: #4a4a4a;
    --ink-soft: #5a5a5a;
    --paper: #ffffff;
    --backdrop: #d9d9d9;
    --signature-fill: #ececec;
  }
  * { box-sizing: border-box; margin: 0; padding: 0; }
  html, body { width: 1200px; height: 1159px; overflow: hidden; }
  body {
    background: var(--backdrop);
    display: flex; align-items: center; justify-content: center;
    font-family: "Arimo", Arial, sans-serif;
  }
  .letterhead {
    position: relative;
    width: 866px; height: 1120px;
    background: var(--paper);
    overflow: hidden;
    box-shadow: 0 2px 10px rgba(0,0,0,.15);
  }
  .brand {
    position: absolute; left: 70px; top: 100px;
    display: flex; align-items: center; gap: 14px;
  }
  .brand-dot {
    width: 40px; height: 40px; border-radius: 50%;
    background: var(--gold);
  }
  .brand-name {
    font-family: "Arimo", Arial, sans-serif; font-weight: 700;
    font-size: 22px; color: var(--navy); line-height: 1.15;
    max-width: 190px;
  }
  .contact {
    position: absolute; right: 60px; top: 58px;
    border-left: 2px solid var(--gold);
    padding-left: 14px;
    font-style: normal;
    font-size: 13px; color: var(--ink-soft); line-height: 1.3;
  }
  .contact-name { font-weight: 700; color: var(--navy); font-size: 15px; }
  .contact-role { margin-bottom: 1px; }
  .contact-phone { display: flex; align-items: center; gap: 5px; margin-bottom: 4px; }
  .contact-phone svg { width: 11px; height: 11px; fill: var(--gold); }
  .letter-body {
    position: absolute; left: 120px; top: 340px; width: 620px;
    color: var(--ink); font-size: 14.5px; line-height: 1.35;
  }
  .salutation {
    font-family: "Montserrat", Arial, sans-serif; font-weight: 700;
    font-size: 19px; color: var(--ink); margin-bottom: 18px;
  }
  .letter-body p { margin-bottom: 22px; }
  .closing {
    font-family: "Montserrat", Arial, sans-serif; font-weight: 700;
    font-size: 12px; margin-top: 38px;
  }
  .signature {
    width: 150px; height: 36px; margin-top: 28px;
    background: var(--signature-fill); border-radius: 4px;
  }
  .footer-wave { position: absolute; left: 0; bottom: 0; width: 866px; height: 330px; }
</style>
</head>
<body>
  <main class="letterhead">
    <div class="brand">
      <span class="brand-dot"></span>
      <span class="brand-name">Bluecrest Learning Corps</span>
    </div>

    <address class="contact">
      <div class="contact-name">Dr. Venrel T Oskamp</div>
      <div class="contact-role">CEO</div>
      <div class="contact-phone"><svg viewBox="0 0 24 24" aria-hidden="true"><path d="M6.6 10.8a15 15 0 0 0 6.6 6.6l2.2-2.2a1 1 0 0 1 1-.25 11.4 11.4 0 0 0 3.6.6 1 1 0 0 1 1 1V20a1 1 0 0 1-1 1A17 17 0 0 1 3 4a1 1 0 0 1 1-1h3.5a1 1 0 0 1 1 1c0 1.25.2 2.45.6 3.6a1 1 0 0 1-.25 1z"/></svg>(703) 482-1736</div>
      <div class="contact-name">Marisa Deltoft</div>
      <div class="contact-role">Respresentative</div>
      <div class="contact-phone"><svg viewBox="0 0 24 24" aria-hidden="true"><path d="M6.6 10.8a15 15 0 0 0 6.6 6.6l2.2-2.2a1 1 0 0 1 1-.25 11.4 11.4 0 0 0 3.6.6 1 1 0 0 1 1 1V20a1 1 0 0 1-1 1A17 17 0 0 1 3 4a1 1 0 0 1 1-1h3.5a1 1 0 0 1 1 1c0 1.25.2 2.45.6 3.6a1 1 0 0 1-.25 1z"/></svg>(301) 647-2208</div>
      <div>4719 Pellham Court<br>Carrowmede Station VA 22187</div>
    </address>

    <article class="letter-body">
      <h1 class="salutation">Dear Mr. Halvorsen,</h1>
      <p>Lorem ipsum dolor sit amet, consectetuer adipiscing elit, sed diam nonmmy nibh euismod tincidunt ut laor eet dolore magna aliquam erat volutpat. Ut wisi enim ad minim veniam, quis nostrud exerci tationmcorper suscipit lobortis nisl ut aliquip ex ea commodo consequat. Duis autem vel eum iriure dolor in hendrerit in vulputate velit esse molestie consequat, vel illum dolore eu feugiat</p>
      <p>Rorem ipsum dolor sit amet, consectetuer adipiscing elit, sed diam nonmmy nibh euismod tincidunt ut laor eet dolore magna aliquam erat volutpat. Ut wisi enim ad minim veniam, quis nostrud exerci tationmcorper suscipit lobortis nisl ut aliquip ex ea commodo consequat. Duis autem vel eum iriure dolor in hendrerit in vulputate velit esse molest</p>
      <p>Dorem ipsum dolor sit amet, consectetuer adipiscing elit, sed diam nonmmy nibh euismod tincidunt ut laor eet dolore magna aliquam erat volutpat. Ut wisi enim ad minim veniam, quis nostrud exerci tationmcorper suscipit lobortis nisl ut aliquip ex ea commodo consequat. Duis autem vel eum iriure dolor in hendrerit in suscipit lobortis nisl ut aliquip ex ea commodo consequat. Duis autem vel eum iriure dolor in hendrerit in vulputate velit esse molestie consequat, vel illum</p>
      <p>Sorem ipsum dolor sit amet, consectetuer adipiscing elit, sed diam nonmmy nibh euismod tincidunt ut laor eet dolore magna aliquam erat volutpat. Ut wisi enim ad minim veniam, quis nostrud exerci tationmcorper suscipit lobortis nisl ut aliquip ex ea commodo consequat. Duis autem vel eum iriure dolor in</p>
      <div class="closing">Sincerely,</div>
      <div class="signature" role="img" aria-label="Handwritten signature"></div>
    </article>

    <svg class="footer-wave" viewBox="0 0 866 330" preserveAspectRatio="none" aria-hidden="true">
      <path d="M150 292 C 450 250, 720 150, 866 0 L 866 14 C 720 160, 460 260, 150 292 Z" fill="var(--navy)"/>
      <path d="M0 300 C 380 300, 680 200, 866 40 L 866 330 L 0 330 Z" fill="var(--gold)"/>
    </svg>
  </main>
</body>
</html>
```